Colin Vardek Business card

Hey there, I’m hoping to have a business card designed. I’m in Real estate and just switched to a new Brokerage called: The Harbourline Property Group

The back could just be the company name maybe or whatever looks good!

I’ve attached some logos of our company and some cards my buddy had done up.

On the card:
Colin Vardek
colinvardek@mailora.com
587-412-9065
colinvardek.ca

Target Market(s)

Home buyers and sellers

Industry/Entity Type

Real Estate

Contact Information for Business Card

just looking for a cool and modern design with my picture on it. I like the idea of Black and red being used.

Requirements
Must have
• all the details provided. I'm open to anything. Just want a professional looking card.

```html
<!DOCTYPE html>
<html lang="en">
<head>
<meta charset="utf-8">
<title>Colin Vardek – Business Card</title>
<link href="https://fonts.googleapis.com/css2?family=Montserrat:wght@800&family=Roboto:wght@400;500&display=swap" rel="stylesheet">
<style>
  :root {
    --page-bg: #2b2b2d;
    --card-bg: #232226;
    --card-edge: #d0173a;
    --accent-red: #d51c3c;
    --text-white: #ffffff;
    --text-soft: #e9e9ec;
    --photo-dark: #1d1c20;
    --photo-mid: #3a3a40;
  }
  * { margin: 0; padding: 0; box-sizing: border-box; }
  html, body {
    width: 1200px; height: 852px; overflow: hidden;
    background: var(--page-bg);
  }
  .canvas { position: relative; width: 1200px; height: 852px; }

  .card {
    position: absolute;
    width: 560px; height: 320px;
    background: var(--card-bg);
    border-radius: 22px;
    border-bottom: 4px solid var(--card-edge);
    border-left: 2px solid var(--card-edge);
    overflow: hidden;
  }
  .card--back  { left: 60px;  top: 70px; }
  .card--front { left: 580px; top: 462px; }

  .brand {
    position: absolute;
    display: flex; align-items: center; gap: 14px;
  }
  .brand__mark {
    width: 16px; height: 16px;
    background: var(--accent-red);
    flex: none;
  }
  .brand__name {
    font-family: "Montserrat", sans-serif;
    font-weight: 800;
    color: var(--text-white);
    text-transform: uppercase;
    line-height: 1.05;
    letter-spacing: 0.5px;
    white-space: nowrap;
  }
  .card--back .brand { left: 70px; top: 118px; }
  .card--back .brand__name { font-size: 34px; }

  .card--front .brand { left: 48px; top: 62px; }
  .card--front .brand__mark { width: 13px; height: 13px; }
  .card--front .brand__name { font-size: 20px; letter-spacing: 0.3px; }

  .portrait {
    position: absolute;
    right: 0; top: 0;
    width: 210px; height: 320px;
    background: linear-gradient(180deg, var(--photo-mid) 0%, var(--photo-dark) 100%);
  }

  .contact { position: absolute; left: 48px; top: 186px; }
  .contact__accent {
    position: absolute; left: -48px; top: 8px;
    width: 10px; height: 34px;
    background: var(--accent-red);
  }
  .contact__name {
    font-family: "Roboto", sans-serif;
    font-weight: 500;
    font-size: 22px;
    color: var(--accent-red);
    margin-bottom: 12px;
  }
  .contact__list { list-style: none; }
  .contact__item {
    display: flex; align-items: center; gap: 10px;
    font-family: "Roboto", sans-serif;
    font-weight: 400;
    font-size: 15px;
    color: var(--text-soft);
    line-height: 24px;
  }
  .contact__icon { width: 14px; height: 14px; flex: none; }
</style>
</head>
<body>
<div class="canvas">

  <section class="card card--back" aria-label="Card back">
    <div class="brand">
      <span class="brand__mark"></span>
      <span class="brand__name">The Harbourline<br>Property Group</span>
    </div>
  </section>

  <section class="card card--front" aria-label="Card front">
    <div class="brand">
      <span class="brand__mark"></span>
      <span class="brand__name">The Harbourline<br>Property Group</span>
    </div>

    <div class="portrait" role="img" aria-label="Portrait photo of Colin Vardek in a dark blazer and white shirt"></div>

    <div class="contact">
      <span class="contact__accent"></span>
      <p class="contact__name">Colin Vardek</p>
      <ul class="contact__list">
        <li class="contact__item">
          <svg class="contact__icon" viewBox="0 0 16 16" aria-hidden="true">
            <path fill="#d51c3c" d="M3.5 1.5l2.5 0 1 3.5-1.6 1.2a8 8 0 0 0 4.4 4.4L11 9l3.5 1v2.5c0 1-1 2-2 2A11 11 0 0 1 1.5 3.5c0-1 1-2 2-2z"/>
          </svg>
          587-412-9065
        </li>
        <li class="contact__item">
          <svg class="contact__icon" viewBox="0 0 16 16" aria-hidden="true">
            <rect x="1" y="3" width="14" height="10" rx="1.5" fill="#d51c3c"/>
            <path d="M1.5 4l6.5 5 6.5-5" fill="none" stroke="#232226" stroke-width="1.4"/>
          </svg>
          colinvardek@mailora.com
        </li>
        <li class="contact__item">
          <svg class="contact__icon" viewBox="0 0 16 16" aria-hidden="true">
            <circle cx="8" cy="8" r="7" fill="#d51c3c"/>
            <path d="M1 8h14M8 1c-3 3.5-3 10.5 0 14M8 1c3 3.5 3 10.5 0 14" fill="none" stroke="#232226" stroke-width="1.1"/>
          </svg>
          colinvardek.ca
        </li>
      </ul>
    </div>
  </section>

</div>
</body>
</html>
```